Moravel Aesthetic Doctor

I require an elegant, luxurious looking business card for my aesthetic business. I am a doctor and that will set me aside from competitors. I am planning to provide home and spa based treatments to clients with high expectations. I have attached my logo.

```html
<!DOCTYPE html>
<html lang="en">
<head>
<meta charset="utf-8">
<title>Moravel Aesthetic Doctor – Business Card</title>
<link rel="stylesheet" href="https://fonts.googleapis.com/css2?family=Marcellus&family=Montserrat:wght@400;500&family=Lato:wght@400&display=swap">
<style>
  :root {
    --backdrop: #dcdde2;
    --navy-deep: #1f1e72;
    --navy-light: #3c3f9e;
    --wave-blue: #5fb3e0;
    --wave-pale: #9fd3ec;
    --silver: #c9c6d6;
    --logo-grey: #8c8c92;
    --accent-blue: #2f8fd6;
    --ink: #555559;
    --paper: #ffffff;
  }
  * { box-sizing: border-box; margin: 0; padding: 0; }
  html, body { width: 1200px; height: 800px; overflow: hidden; }
  body { background: var(--backdrop); position: relative; font-family: "Montserrat", sans-serif; }

  .card {
    position: absolute;
    left: 389px;
    width: 461px;
    height: 263px;
    overflow: hidden;
  }

  /* Front */
  .card--front {
    top: 93px;
    background: linear-gradient(215deg, var(--navy-light) 0%, var(--navy-deep) 75%);
  }
  .front-mark {
    position: absolute;
    left: 20px; top: 22px;
    width: 220px; height: 220px;
    border-radius: 50%;
    background: radial-gradient(circle at 40% 40%, var(--wave-pale), var(--wave-blue));
    opacity: 0.55;
  }
  .front-brand {
    position: absolute;
    right: 26px; top: 168px;
    text-align: right;
    color: var(--silver);
    font-family: "Marcellus", serif;
    font-weight: 400;
  }
  .front-brand .brand-name { display: block; font-size: 40px; line-height: 1; letter-spacing: 1px; }
  .front-brand .brand-role { display: block; font-size: 15.5px; letter-spacing: 1.6px; margin-top: 6px; }
  .front-tagline {
    position: absolute;
    right: 26px; top: 233px;
    color: var(--paper);
    font-family: "Lato", sans-serif;
    font-size: 11px;
  }

  /* Back */
  .card--back {
    top: 422px;
    background: linear-gradient(160deg, #f1f1f3 0%, var(--paper) 55%, #f6f6f8 100%);
  }
  .back-logo {
    position: absolute;
    left: 44px; top: 105px;
    display: flex; align-items: center; gap: 8px;
  }
  .back-logo .logo-circle {
    width: 50px; height: 50px;
    border-radius: 50%;
    border: 2px solid var(--logo-grey);
  }
  .back-logo .logo-text {
    color: var(--logo-grey);
    font-family: "Marcellus", serif;
    font-weight: 400;
  }
  .back-logo .brand-name { display: block; font-size: 27px; line-height: 1; letter-spacing: 0.5px; }
  .back-logo .brand-role { display: block; font-size: 10.5px; letter-spacing: 1.3px; margin-top: 4px; }

  .divider {
    position: absolute;
    left: 237px; top: 84px;
    width: 1px; height: 95px;
    background: var(--accent-blue);
  }
  .contact {
    position: absolute;
    left: 251px; top: 82px;
    color: var(--ink);
  }
  .contact .person { color: var(--accent-blue); font-size: 13px; font-weight: 500; }
  .contact .person small { color: var(--ink); font-size: 7px; font-weight: 400; margin-left: 3px; }
  .contact .credential { font-size: 10.5px; line-height: 13px; margin-top: 4px; }
  .contact-list { list-style: none; margin-top: 12px; font-size: 10.5px; line-height: 14px; }
  .contact-list li { display: flex; align-items: center; gap: 5px; }
  .contact-list svg { width: 8px; height: 8px; fill: var(--accent-blue); flex: none; }
  .social { display: inline-flex; gap: 6px; margin-left: 14px; }
  .social span { width: 8px; height: 8px; border-radius: 50%; background: var(--accent-blue); }

  .services {
    position: absolute;
    left: 0; right: 0; top: 230px;
    text-align: center;
    color: var(--ink);
    font-family: "Lato", sans-serif;
    font-size: 10.5px;
  }
</style>
</head>
<body>

<section class="card card--front">
  <div class="front-mark"></div>
  <div class="front-brand">
    <span class="brand-name">MORAVEL</span>
    <span class="brand-role">AESTHETIC DOCTOR</span>
  </div>
  <p class="front-tagline">Home and Spa Based Treatments</p>
</section>

<section class="card card--back">
  <div class="back-logo">
    <div class="logo-circle"></div>
    <div class="logo-text">
      <span class="brand-name">MORAVEL</span>
      <span class="brand-role">AESTHETIC DOCTOR</span>
    </div>
  </div>

  <div class="divider"></div>

  <div class="contact">
    <p class="person">Dr Elise Varden <small>MRCPCH MD</small></p>
    <p class="credential">Australasian Diploma<br>of Aesthetic Medicine</p>
    <ul class="contact-list">
      <li>
        <svg viewBox="0 0 10 10" aria-hidden="true"><path d="M2 0.5 L3.8 2.6 L2.9 3.8 C3.5 5 4.9 6.4 6.2 7.1 L7.4 6.2 L9.5 8 L8.4 9.5 C4.5 9.2 0.8 5.5 0.5 1.6 Z"/></svg>
        0800 555 019
      </li>
      <li>
        <svg viewBox="0 0 10 10" aria-hidden="true"><path d="M0.5 2 H9.5 V8.5 H0.5 Z M1.2 2.6 L5 5.6 L8.8 2.6" stroke="#fff" stroke-width="0.6"/></svg>
        elise@moravel.co.nz
      </li>
      <li>
        <svg viewBox="0 0 10 10" aria-hidden="true"><circle cx="5" cy="5" r="4.5"/><path d="M0.5 5 H9.5 M5 0.5 V9.5 M1.5 2.7 H8.5 M1.5 7.3 H8.5" stroke="#fff" stroke-width="0.5" fill="none"/></svg>
        www.moravel.co.nz
        <span class="social"><span></span><span></span></span>
      </li>
    </ul>
  </div>

  <p class="services">Dermal injectables - Plasma facials - Microneedling Skin boosters - Excessive sweating</p>
</section>

</body>
</html>
```